Facebook template for supermarket

I need a new fresh Facebook template in which I can paste an image that changes depending on the content of the Facebook post. I need to be able to change the design in Adobe Photoshop. It concerns the FB page of a local supermarket.
I once made a template myself, but I'm not satisfied with it.
Check the supermarket's website to see the supermarket's color scheme and style. The supermarket is a forerunner in the field of fresh products from local suppliers and has a wide range of organic products.
The slogan of the supermarket is 'With VELDO you find fine meals, your street and true friends'. The supermarket has a strong bond with the neighborhood and the inhabitants.
I have added my self-made template as an example. At the bottom right is the name of the owners of the supermarket.

```html
<!DOCTYPE html>
<html lang="nl">
<head>
<meta charset="utf-8">
<title>VELDO – Facebook post</title>
<link rel="stylesheet" href="https://fonts.googleapis.com/css2?family=Montserrat:wght@500;600;700;800&display=swap">
<style>
  :root {
    --cream: #fbf3e8;
    --lime: #7ab51d;
    --brand-green: #74b72a;
    --forest: #237a44;
    --ink: #111111;
    --white: #ffffff;
  }
  * { margin: 0; padding: 0; box-sizing: border-box; }
  html, body { width: 1200px; height: 1200px; overflow: hidden; background: var(--cream); }
  .post {
    position: relative;
    width: 1200px;
    height: 1200px;
    background: var(--cream);
    font-family: "Montserrat", sans-serif;
    overflow: hidden;
  }
  .shapes { position: absolute; inset: 0; }
  .brand { position: absolute; left: 57px; top: 84px; color: var(--brand-green); font-weight: 700; }
  .brand-name { font-size: 42px; line-height: 1; letter-spacing: 1px; }
  .brand-owners { font-size: 24px; margin-top: 18px; }
  .headline { position: absolute; left: 48px; top: 398px; color: var(--white); }
  .headline-light { display: block; font-size: 75px; font-weight: 500; line-height: 1.05; }
  .headline-bold { display: block; font-size: 75px; font-weight: 700; line-height: 1.05; }
  .intro {
    position: absolute; left: 51px; top: 687px; width: 500px;
    color: var(--white); font-size: 26px; font-weight: 500; line-height: 1.45;
  }
  .join-button {
    position: absolute; left: 52px; top: 893px; width: 157px; height: 43px;
    background: var(--ink); color: var(--lime); border-radius: 8px;
    font-size: 23px; font-weight: 700; display: flex; align-items: center; justify-content: center;
  }
  .website { position: absolute; left: 52px; top: 948px; color: var(--white); font-size: 25px; font-weight: 500; }
  .contact { position: absolute; right: 144px; top: 1034px; text-align: right; color: var(--ink); }
  .contact-label { font-size: 29px; font-weight: 700; }
  .contact-phone { font-size: 40px; font-weight: 700; margin-top: 4px; }
  .contact-icon { position: absolute; left: 1085px; top: 1038px; width: 60px; height: 70px; }
</style>
</head>
<body>
<main class="post">
  <svg class="shapes" width="1200" height="1200" viewBox="0 0 1200 1200">
    <defs>
      <linearGradient id="storeTone" x1="0" y1="0" x2="0" y2="1">
        <stop offset="0" stop-color="#eef3f7"/>
        <stop offset="0.45" stop-color="#c9d6e0"/>
        <stop offset="0.7" stop-color="#d89a3a"/>
        <stop offset="1" stop-color="#c8ccd2"/>
      </linearGradient>
    </defs>
    <rect class="photo-slot" role="img" aria-label="Photo of the supermarket interior with fruit displays and shopping carts" x="500" y="127" width="700" height="796" fill="url(#storeTone)"/>
    <polygon class="accent-triangle" points="500,127 725,282 450,282" fill="var(--forest)"/>
    <polygon class="text-panel" points="0,282 725,282 462,1080 0,1080" fill="var(--lime)"/>
  </svg>

  <header class="brand">
    <div class="brand-name">VELDO</div>
    <div class="brand-owners">Bram en Lotte Visser</div>
  </header>

  <h1 class="headline">
    <span class="headline-light">Lorem Ipsum</span>
    <span class="headline-bold">is simply</span>
    <span class="headline-bold">dummy text</span>
  </h1>

  <p class="intro">&nbsp;Lorem Ipsum has been the indus-<br>try's standard dummy text ever<br>since the 1500s,</p>

  <div class="join-button">JOIN US</div>
  <div class="website">www.websitename.com</div>

  <div class="contact">
    <div class="contact-label">More info</div>
    <div class="contact-phone">+000 123 456 789</div>
  </div>

  <svg class="contact-icon" viewBox="0 0 60 70" aria-hidden="true">
    <rect x="4" y="2" width="48" height="64" rx="6" fill="var(--brand-green)"/>
    <rect x="48" y="12" width="8" height="10" rx="2" fill="var(--brand-green)"/>
    <rect x="48" y="30" width="8" height="10" rx="2" fill="var(--brand-green)"/>
    <rect x="48" y="48" width="8" height="10" rx="2" fill="var(--brand-green)"/>
    <path d="M17 22c2-2 5-2 6 1l2 5c1 2 0 3-2 4 2 5 5 8 10 10 1-2 2-3 4-2l5 2c3 1 3 4 1 6-3 3-7 4-12 1-8-4-13-10-16-18-1-4 0-7 2-9z" fill="none" stroke="var(--white)" stroke-width="3" stroke-linejoin="round"/>
  </svg>
</main>
</body>
</html>
```